Web Design Project and logo

We need a new web design and logo for www.kz7ventures.com

It is a mobile app development company. Site needs to look very cool/trendy as does the new logo.

Looking for the design (uncoded) and the logo file that my developers can then use to build out the site.

An example of a nice competitor site is www.thecodegarage.com

We want something that looks fresh, clean and hip.

Also development of business cards.

Target Market(s)

Small to mid sized companies

Industry/Entity Type

Business

Requirements
Must have
• Ability to request a quote
Should look very trendy like www.thecodegarage.com as an example of a competitor site

```html
<!DOCTYPE html>
<html lang="en">
<head>
<meta charset="utf-8">
<title>KZ7 Ventures</title>
<link href="https://fonts.googleapis.com/css2?family=Arimo:wght@400&family=Roboto:wght@300;400&display=swap" rel="stylesheet">
<style>
  :root {
    --brand-teal: #258a94;
    --accent-red: #d0381a;
    --text-dark: #45454f;
    --nav-text: #3c3c44;
    --border-grey: #b9bcc0;
    --nav-top: #fbfbfb;
    --nav-bottom: #e9eaeb;
    --sky-light: #d9eef8;
    --sky-mid: #8cc8e8;
    --sky-deep: #3f93c8;
    --social-blue: #4a67a8;
    --social-sky: #7cc3e4;
    --social-orange: #f0862a;
  }
  * { margin: 0; padding: 0; box-sizing: border-box; }
  html, body { width: 1200px; height: 1000px; overflow: hidden; background: #fff; }
  body { position: relative; font-family: "Arimo", Arial, sans-serif; color: var(--text-dark); }

  .brand { position: absolute; left: 33px; top: 60px; display: flex; align-items: center; gap: 18px; }
  .brand-mark { width: 77px; height: 77px; background: var(--brand-teal); border-radius: 14px; }
  .brand-name { font-size: 40px; color: var(--brand-teal); letter-spacing: 0.5px; }

  .search { position: absolute; left: 555px; top: 31px; width: 189px; height: 28px;
    border: 1px solid var(--border-grey); border-radius: 5px; background: #fff;
    display: flex; align-items: center; justify-content: space-between; padding: 0 8px 0 9px;
    font-family: "Roboto", Arial, sans-serif; font-weight: 300; font-size: 18px; color: #777; }

  .social { position: absolute; top: 28px; left: 1038px; display: flex; gap: 16px; list-style: none; }
  .social li { width: 32px; height: 32px; border-radius: 5px; }
  .social .s1 { background: var(--social-blue); }
  .social .s2 { background: var(--social-sky); }
  .social .s3 { background: var(--social-orange); }

  .main-nav { position: absolute; left: 552px; top: 91px; width: 616px; height: 37px;
    border: 1px solid var(--border-grey); border-radius: 5px;
    background: linear-gradient(var(--nav-top), var(--nav-bottom)); display: flex; list-style: none; }
  .main-nav li { height: 100%; display: flex; align-items: center; justify-content: center;
    font-family: "Roboto", Arial, sans-serif; font-weight: 300; font-size: 14px; color: var(--nav-text);
    border-right: 1px solid #a9acb0; }
  .main-nav li:last-child { border-right: 0; }
  .main-nav .active, .footer-nav .active { color: var(--accent-red); }

  .hero { position: absolute; left: 33px; top: 169px; width: 1134px; height: 387px; overflow: hidden;
    background: radial-gradient(ellipse at 40% 60%, #fff 0%, var(--sky-light) 25%, var(--sky-mid) 60%, var(--sky-deep) 100%); }
  .hero-title { position: absolute; left: 205px; top: 105px; font-size: 92px; color: #fff;
    letter-spacing: -2px; text-shadow: 3px 4px 6px rgba(0,0,0,0.3); }

  .feature { position: absolute; }
  .feature-icon { position: absolute; border-radius: 4px; }
  .feature-title { position: absolute; font-size: 26px; color: var(--text-dark); white-space: nowrap; }
  .feature-text { position: absolute; font-size: 20px; line-height: 25px; color: var(--text-dark); white-space: nowrap; }

  .footer-nav { position: absolute; top: 951px; left: 0; width: 1200px; height: 22px; list-style: none;
    font-family: "Roboto", Arial, sans-serif; font-weight: 300; font-size: 17px; color: var(--nav-text); }
  .footer-nav li { position: absolute; top: 0; }
</style>
</head>
<body>
  <header>
    <div class="brand">
      <span class="brand-mark"></span>
      <span class="brand-name">KZ7 Ventures</span>
    </div>

    <div class="search">
      <span>Search</span>
      <svg width="20" height="20" viewBox="0 0 20 20" aria-hidden="true">
        <circle cx="8" cy="8" r="6" fill="none" stroke="#666" stroke-width="1.5"/>
        <line x1="12.5" y1="12.5" x2="18" y2="18" stroke="#666" stroke-width="2.5" stroke-linecap="round"/>
      </svg>
    </div>

    <ul class="social" aria-label="Social links">
      <li class="s1"></li><li class="s2"></li><li class="s3"></li>
    </ul>

    <ul class="main-nav">
      <li class="active" style="width:85px">HOME</li>
      <li style="width:157px">OUR SERVICES</li>
      <li style="width:95px">A BOUT</li>
      <li style="width:141px">LATEST NEWS</li>
      <li style="width:136px">CONTACT US</li>
    </ul>
  </header>

  <section class="hero" role="img" aria-label="Banner photo of a globe and a smartphone in front of a blue cloudy sky over water">
    <div class="hero-title">Sample image</div>
  </section>

  <main>
    <article class="feature">
      <div class="feature-icon" role="img" aria-label="Smartphone" style="left:74px;top:572px;width:45px;height:75px;background:linear-gradient(#bfe6ee,#4c8e9c);border-radius:8px"></div>
      <h2 class="feature-title" style="left:130px;top:615px;font-weight:400">Mobile Services</h2>
      <p class="feature-text" style="left:79px;top:664px">Lorem ipsum dolor sit amet, con<br>sectetuer adipiscing elit. Aenean<br>commodo ligula eget dolor. Aen<br>ean massa. Cum sociis natoque<br>penatibus et magnis dis parturi<br>ent montes, nascetur ridiculus<br>mus. Donec quam felis, ultricies</p>
    </article>

    <article class="feature">
      <div class="feature-icon" role="img" aria-label="Hand holding a smartphone with app icons" style="left:389px;top:571px;width:87px;height:97px;background:linear-gradient(135deg,#f4c9a8,#4a6fa0)"></div>
      <h2 class="feature-title" style="left:489px;top:616px;font-weight:400">Quality</h2>
      <p class="feature-text" style="left:439px;top:668px">Lorem ipsum dolor sit amet, con<br>sectetuer adipiscing elit. Aenean<br>commodo ligula eget dolor. Aen<br>ean massa. Cum sociis natoque<br>penatibus et magnis dis parturi<br>ent montes, nascetur ridiculus<br>mus. Donec quam felis, ultricies</p>
    </article>

    <article class="feature">
      <div class="feature-icon" role="img" aria-label="Hands using a tablet with app icons" style="left:818px;top:578px;width:82px;height:82px;background:linear-gradient(135deg,#2a4f8a,#d9a88a);border-radius:0"></div>
      <h2 class="feature-title" style="left:913px;top:609px;font-weight:400">Join Us</h2>
      <p class="feature-text" style="left:831px;top:668px">Lorem ipsum dolor sit amet, con<br>sectetuer adipiscing elit. Aenean<br>commodo ligula eget dolor. Aen<br>ean massa. Cum sociis natoque<br>penatibus et magnis dis parturi<br>ent montes, nascetur ridiculus<br>mus. Donec quam felis, ultricies</p>
    </article>
  </main>

  <footer>
    <ul class="footer-nav">
      <li class="active" style="left:330px">HOME</li>
      <li style="left:411px">OUR SERVICES</li>
      <li style="left:568px">A BOUT</li>
      <li style="left:658px">LATEST NEWS</li>
      <li style="left:800px">CONTACT US</li>
    </ul>
  </footer>
</body>
</html>
```